Upmarket Dessert Lounge needs a Business Card Design

We are an upmarket dessert lounge needing a business card to match our image.

We want something that is simple yet beautiful, feminine, classy, sophisticated and elegant. We want it to stand out and don't mind if it is bold.

The design should include our logo and colours of red or maroon with gold highlights. We don't mind if black is used.

Marlow & Quince

Target Market(s)

For those who like to indulge or treat themselves and give in to their temptations on good quality desserts.

Industry/Entity Type

Business

Requirements
Must have
• Must include our logo and our name

Marlow & Quince

M & Q

```html
<!DOCTYPE html>
<html lang="en">
<head>
<meta charset="utf-8">
<title>Marlow &amp; Quince — Business Card</title>
<link rel="stylesheet" href="https://fonts.googleapis.com/css2?family=Open+Sans:wght@400;600;700&display=swap">
<style>
  :root {
    --maroon: #7a1416;
    --ink: #333333;
    --card: #ffffff;
    --backdrop: #e4e4e4;
  }
  * { box-sizing: border-box; margin: 0; padding: 0; }
  html, body {
    width: 956px;
    height: 1200px;
    overflow: hidden;
    background: var(--backdrop);
    font-family: "Open Sans", Arial, sans-serif;
    color: var(--ink);
  }
  .canvas { position: relative; width: 956px; height: 1200px; }
  .card {
    position: absolute;
    background: var(--card);
    border-radius: 30px;
    overflow: hidden;
    box-shadow: 0 6px 14px rgba(0,0,0,0.25);
  }
  .card--front { left: 78px; top: 96px; width: 798px; height: 455px; }
  .card--back  { left: 74px; top: 632px; width: 797px; height: 456px; }
  .swoosh { position: absolute; inset: 0; width: 100%; height: 100%; }
  .wordmark {
    position: absolute;
    color: var(--maroon);
    font-weight: 600;
    text-align: center;
    white-space: nowrap;
  }
  .card--front .wordmark {
    left: 0; width: 700px; top: 108px;
    font-size: 40px;
    letter-spacing: 2px;
  }
  .card--back .wordmark {
    left: 0; right: 0; top: 160px;
    font-size: 112px;
    line-height: 1;
  }
  .contact {
    position: absolute;
    left: 0; width: 700px; top: 276px;
    text-align: center;
    font-size: 19.5px;
  }
  .contact__name { font-size: 22px; margin-bottom: 14px; }
  .contact__name strong { font-weight: 700; }
  .contact__line { margin-bottom: 17px; }
  .contact__line b { font-weight: 700; }
</style>
</head>
<body>
<div class="canvas">
  <section class="card card--front">
    <svg class="swoosh" viewBox="0 0 798 455" preserveAspectRatio="none" aria-hidden="true">
      <path d="M552 0 C 760 40 830 260 672 455 L798 455 L798 0 Z" fill="var(--maroon)"/>
      <path d="M642 0 C 790 60 825 250 738 420 C 800 250 775 80 698 0 Z" fill="var(--card)"/>
    </svg>
    <div class="wordmark">MARLOW &amp; QUINCE</div>
    <div class="contact">
      <p class="contact__name"><strong>Your Name -</strong> Designation</p>
      <p class="contact__line"><b>p</b> : 123-456-7890 &nbsp;|&nbsp; <b>c</b> : 123-456-7890 &nbsp;|&nbsp; <b>f</b> : 123-456-7890</p>
      <p class="contact__line"><b>e</b> : name@yourwebsite.com &nbsp;|&nbsp; <b>w</b> : www.marlow&amp;quince.com</p>
      <p class="contact__line">0000, Street Name, City Name, Country Code.</p>
    </div>
  </section>

  <section class="card card--back">
    <div class="wordmark">M &amp; Q</div>
  </section>
</div>
</body>
</html>
```